Thoroughbred Racing Partnership needs web design

Glimmer of Laurel Partners is a management group who buys horses and races them on both the West and East coasts. The premise of the business is for an investment as little as $500, anyone can be a partner and own a percentage of a horse(s). This is a low cost way of getting involved in the exciting sport of Thoroughbred Racing, without shouldering the heavy financial responsibility. Our target market is mostly males 40+ but we want to include all target markets. We are looking for something very clean and professional, we want to give an image of success. Nothing overly "artsy." I have included the logo in which you can incorporate in the site. Also, the logo colors will be the colors of our "silks." The silks are what the jockey wears and will be an important marketing tool for GOL. We would like a very prominent picture of a racehorse somewhere on the homepage, we want to make it clear that is a website for Horseracing partnerships.

On the top of the site, it should say "Glimmer of Laurel" (on the top)
and below that "Thoroughbred Racing Partnerships." (below that)

The main sections, which should be across the top are:

Home
About Us
Ownership
Stable Roster
News
Contact us

Some of these will have drop down menus.

An example of a competitor website that we like is: www.harrowgatefarm.example
An example of a competitor website that we don't like is: www.paddockvue.example
Updates

Project Deadline Extended
Reason: We have a Board of Directors meeting on the 22nd and we will be making a decision on that day. I'm giving an extension so that all designers are able to submit their designs by the 22nd. Thank you!

Target Market(s)

40+ males

Industry/Entity Type

Business

Requirements
Must have
• our logo must be on the site. We would like at least one bold image of a thoroughbred horse in action. The picture is going to tell the story so it needs to be very eye-catching.

Our slogan should also be included on the website, "Experience the thrill of owning a Racehorse."
Should not have
• cartoons, artsy pictures, pictures of Steeplechase horses or "jumpers." This partnership is for racehorses only, there is not jumping involved with the horses.

```html
<!DOCTYPE html>
<html lang="en">
<head>
<meta charset="utf-8">
<title>Glimmer of Laurel Partners – Thoroughbred Racing Partnerships</title>
<link href="https://fonts.googleapis.com/css2?family=Roboto+Condensed:wght@400;700&family=PT+Sans:wght@400;700&display=swap" rel="stylesheet">
<style>
:root{
  --header-bg:#34373c;
  --nav-top:#5d5f63;
  --nav-bottom:#46484c;
  --nav-divider:#2f3134;
  --content-bg:#1b1b1b;
  --footer-bg:#282828;
  --bottom-bg:#1f1f1f;
  --white:#ffffff;
  --muted:#a9abae;
  --body-text:#bdbdbd;
  --footer-text:#c8c8c8;
  --accent:#1597d8;
  --btn-top:#1275b7;
  --btn-bottom:#0a5590;
  --rule:#333333;
}
*{box-sizing:border-box;margin:0;padding:0}
html,body{width:1179px;height:1200px;overflow:hidden;background:var(--content-bg)}
body{position:relative;font-family:"PT Sans",sans-serif;color:var(--white)}
.heading{font-family:"Roboto Condensed",sans-serif;text-transform:uppercase;font-weight:400}

/* header */
.site-header{position:absolute;left:0;top:0;width:1179px;height:78px;background:var(--header-bg)}
.brand{position:absolute;left:178px;top:14px;width:104px;text-align:center}
.brand-name{font-family:"Roboto Condensed",sans-serif;font-weight:700;font-size:30px;line-height:32px;color:var(--white);letter-spacing:2px}
.brand-domain{font-family:"Roboto Condensed",sans-serif;font-weight:700;font-size:12px;line-height:16px;color:var(--white)}
.site-title{position:absolute;left:370px;top:16px;font-size:19px;line-height:22px;color:var(--white)}
.site-tagline{position:absolute;left:370px;top:44px;font-size:13.5px;line-height:16px;color:var(--muted)}
.btn{display:flex;align-items:center;justify-content:center;gap:6px;background:linear-gradient(var(--btn-top),var(--btn-bottom));color:var(--white);font-size:10.5px;text-transform:uppercase;border-radius:2px;position:absolute}
.btn-login{left:838px;top:25px;width:69px;height:26px;font-family:"Roboto Condensed",sans-serif;font-size:12px}
.btn-register{left:914px;top:25px;width:87px;height:26px;font-family:"Roboto Condensed",sans-serif;font-size:12px}

/* nav */
.main-nav{position:absolute;left:0;top:78px;width:1179px;height:48px;background:linear-gradient(var(--nav-top),var(--nav-bottom));border-top:1px solid #6a6c70}
.main-nav a{position:absolute;top:0;height:47px;line-height:47px;text-align:center;font-family:"Roboto Condensed",sans-serif;font-size:12px;color:var(--white);text-decoration:none;text-transform:uppercase}
.main-nav .divider{position:absolute;top:0;width:1px;height:47px;background:var(--nav-divider)}

/* hero */
.hero{position:absolute;left:0;top:126px;width:1179px;height:524px;overflow:hidden}
.hero-photo{position:absolute;inset:0;background:
  radial-gradient(ellipse 45% 60% at 72% 62%,#8a4a22 0%,#6d3a1c 45%,rgba(80,50,25,0) 75%),
  radial-gradient(ellipse 20% 30% at 70% 28%,#8a2a32 0%,rgba(138,42,50,0) 80%),
  linear-gradient(180deg,#6f7f86 0%,#3d5236 30%,#2f4a22 55%,#3c6a2a 80%,#2d4f1f 100%)}
.hero-shade{position:absolute;inset:0;background:radial-gradient(ellipse at center,rgba(0,0,0,0) 50%,rgba(0,0,0,.45) 100%)}
.slide-arrow{position:absolute;top:236px;width:52px;height:52px}
.slide-arrow.prev{left:67px}
.slide-arrow.next{left:1044px}
.slogan{position:absolute;left:178px;top:336px}
.slogan-line1{font-size:29px;line-height:34px}
.slogan-line2{font-size:41px;line-height:46px}

/* content */
.content{position:absolute;left:0;top:650px;width:1179px;height:301px;background:var(--content-bg)}
.col-title{position:absolute;top:27px;font-size:19px;line-height:22px}
.welcome{position:absolute;left:178px;top:27px;width:300px}
.welcome .small{font-size:18px;line-height:20px}
.welcome .big{font-size:25px;line-height:28px}
.welcome p{margin-top:20px;font-size:9px;line-height:16px;color:var(--body-text)}
.btn-more{height:25px;font-size:9.5px;font-family:"PT Sans",sans-serif;text-transform:uppercase}
.video{position:absolute;left:504px;top:62px;width:235px;height:189px;background:#222}
.video-frame{position:absolute;left:0;top:0;width:235px;height:169px;background:linear-gradient(90deg,#7f7564 0%,#3a3430 40%,#5a5048 70%,#2c3440 100%)}
.video-bar{position:absolute;left:0;bottom:0;width:235px;height:20px;background:linear-gradient(#2c2c2c,#151515);font-size:9px;color:var(--white)}
.news-item{position:absolute;left:770px;width:230px}
.news-thumb{position:absolute;left:2px;top:0;width:59px;height:59px;border:2px solid #d8d8d8}
.news-text{position:absolute;left:77px;top:0;width:160px;font-size:8.5px;line-height:16px;color:var(--body-text)}
.news-text .title,.news-text .date{color:var(--accent)}
.news-text .date{font-style:italic}
.news-rule{position:absolute;left:772px;top:141px;width:228px;height:1px;background:var(--rule)}

/* footer */
.site-footer{position:absolute;left:0;top:951px;width:1179px;height:199px;background:var(--footer-bg)}
.footer-list{position:absolute;top:27px;list-style:none;font-size:9px;line-height:21.5px;color:var(--footer-text)}
.footer-contact{position:absolute;left:614px;top:27px;font-size:9px;line-height:21.5px;color:var(--footer-text)}
.footer-contact .name{font-weight:700}
.contact-row{display:flex;align-items:center;gap:8px;height:25px}
.social{position:absolute;left:837px;top:24px;list-style:none}
.social li{display:flex;align-items:center;gap:6px;height:30px;font-size:9px;color:var(--footer-text)}
.social .dot{width:20px;height:20px;border-radius:50%;background:#4a4a4a}
.bottom-bar{position:absolute;left:0;top:1150px;width:1179px;height:50px;background:var(--bottom-bg);text-align:center;line-height:46px;font-size:9px;color:var(--muted)}
</style>
</head>
<body>

<header class="site-header">
  <div class="brand">
    <div class="brand-name">GOL</div>
    <div class="brand-domain">GOLPARTNERS.COM</div>
  </div>
  <div class="site-title heading">Glimmer of Laurel</div>
  <div class="site-tagline heading">Thoroughbred Racing Partnerships</div>
  <a class="btn btn-login">Login
    <svg width="6" height="8" viewBox="0 0 6 8"><path d="M1 1l3 3-3 3" stroke="#fff" stroke-width="1.4" fill="none"/></svg></a>
  <a class="btn btn-register">Register
    <svg width="6" height="8" viewBox="0 0 6 8"><path d="M1 1l3 3-3 3" stroke="#fff" stroke-width="1.4" fill="none"/></svg></a>
</header>

<nav class="main-nav">
  <a style="left:176px;width:138px">Home</a>
  <span class="divider" style="left:314px"></span>
  <a style="left:315px;width:137px">About Us</a>
  <span class="divider" style="left:452px"></span>
  <a style="left:453px;width:137px">Ownership</a>
  <span class="divider" style="left:590px"></span>
  <a style="left:591px;width:137px">Stable Roster</a>
  <span class="divider" style="left:728px"></span>
  <a style="left:729px;width:137px">News</a>
  <span class="divider" style="left:866px"></span>
  <a style="left:867px;width:137px">Contact Us</a>
</nav>

<section class="hero">
  <div class="hero-photo" role="img" aria-label="Photo of a jockey in red silks and striped helmet riding a bay thoroughbred racehorse on a green turf track with trees behind"></div>
  <div class="hero-shade"></div>
  <svg class="slide-arrow prev" viewBox="0 0 52 52"><circle cx="26" cy="26" r="24" fill="none" stroke="rgba(255,255,255,.25)" stroke-width="2"/><path d="M31 16L18 26l13 10z" fill="rgba(255,255,255,.2)"/></svg>
  <svg class="slide-arrow next" viewBox="0 0 52 52"><circle cx="26" cy="26" r="24" fill="none" stroke="rgba(255,255,255,.25)" stroke-width="2"/><path d="M21 16l13 10-13 10z" fill="rgba(255,255,255,.2)"/></svg>
  <div class="slogan heading">
    <div class="slogan-line1">Experience the thrill</div>
    <div class="slogan-line2">of owning a racehorse</div>
  </div>
</section>

<main class="content">
  <div class="welcome heading-block">
    <div class="heading small">Welcome to</div>
    <div class="heading big">GOL Partners</div>
    <p>It is a long established fact that a reader will be distracted by the readable content of a page when looking at its layout. The point of using Lorem Ipsum is that it has a more-or-less normal distribution of letters, as opposed to using 'Content here, content here', making it look like readable English. Many desktop publishing packages and web page editors now use Lorem Ipsum as their default model text, and a search for 'lorem ipsum' will uncover many web sites still in their infancy. their default model text, and a search for 'lorem ipsum' will uncover many web sites still in their infancy.</p>
  </div>
  <a class="btn btn-more" style="left:178px;top:236px;width:107px">View More Info</a>

  <div class="col-title heading" style="left:502px">Our Videos</div>
  <div class="video">
    <div class="video-frame" role="img" aria-label="Video still of three men presenting a framed racing award"></div>
    <svg style="position:absolute;left:86px;top:55px" width="62" height="62" viewBox="0 0 62 62"><circle cx="31" cy="31" r="29" fill="rgba(40,40,40,.55)" stroke="rgba(255,255,255,.35)" stroke-width="2"/><path d="M24 18l21 13-21 13z" fill="rgba(255,255,255,.6)"/></svg>
    <div class="video-bar">
      <svg style="position:absolute;left:8px;top:5px" width="10" height="10"><rect x="1" y="0" width="3" height="10" fill="#ccc"/><rect x="6" y="0" width="3" height="10" fill="#ccc"/></svg>
      <svg style="position:absolute;left:30px;top:5px" width="18" height="10"><path d="M0 3h3l4-3v10l-4-3H0z" fill="#888"/><path d="M9 6h1v4H9zM11 4h1v6h-1zM13 2h1v8h-1zM15 0h1v10h-1z" fill="#666"/></svg>
      <span style="position:absolute;left:54px;top:4px">0:04 / 0:30</span>
      <span style="position:absolute;left:113px;top:7px;width:96px;height:6px;background:#000"></span>
      <span style="position:absolute;left:113px;top:7px;width:46px;height:6px;background:#555"></span>
      <span style="position:absolute;left:113px;top:7px;width:6px;height:6px;background:#c0272d"></span>
      <span style="position:absolute;left:117px;top:5px;width:10px;height:10px;border-radius:50%;background:#ddd"></span>
      <svg style="position:absolute;left:216px;top:5px" width="12" height="10"><path d="M0 0h4M0 0v3M12 0H8M12 0v3M0 10h4M0 10V7M12 10H8M12 10V7" stroke="#777" stroke-width="1.5"/></svg>
    </div>
  </div>

  <div class="col-title heading" style="left:770px">Latest News</div>
  <article class="news-item" style="top:64px">
    <div class="news-thumb" role="img" aria-label="Thumbnail photo of a jockey on a racehorse" style="background:linear-gradient(135deg,#6a4a38,#a0452a,#3c5a2a)"></div>
    <div class="news-text"><div class="title">It is a long established fact</div>It is a long established fact that a reader will be distracted...<div class="date">Posted on 27 Aug 2013</div></div>
  </article>
  <div class="news-rule"></div>
  <article class="news-item" style="top:156px">
    <div class="news-thumb" role="img" aria-label="Thumbnail photo of a racehorse at full gallop" style="background:linear-gradient(135deg,#b23a30,#3a2a30,#5a3a2a)"></div>
    <div class="news-text"><div class="title">It is a long established fact</div>It is a long established fact that a reader will be distracted...<div class="date">Posted on 27 Aug 2013</div></div>
  </article>
  <a class="btn btn-more" style="left:773px;top:236px;width:107px">View More News</a>
</main>

<footer class="site-footer">
  <ul class="footer-list" style="left:193px">
    <li>Home</li><li>About Us</li><li>Ownership</li><li>Stable Roster</li><li>News</li><li>Contact us</li>
  </ul>
  <ul class="footer-list" style="left:378px">
    <li>Login</li><li>Register</li><li>Terms &amp; Conditions</li><li>Privacy Policy</li><li>Disclaimer</li>
  </ul>
  <div class="footer-contact">
    <div class="name">GOL PARTNERS</div>
    <div>Street name</div>
    <div>Area Name, Country Name - 1111118</div>
    <div class="contact-row"><svg width="12" height="12" viewBox="0 0 12 12"><path d="M2 1l2 0 1 3-1.5 1a7 7 0 0 0 3.5 3.5L8 7l3 1v2c0 1-1 1-1 1C5 11 1 7 1 2c0 0 0-1 1-1z" fill="#bbb"/></svg>( 1111 ) 111 111,</div>
    <div class="contact-row"><svg width="12" height="12" viewBox="0 0 12 12"><rect x="3" y="0" width="6" height="3" fill="#bbb"/><rect x="0" y="4" width="12" height="5" rx="1" fill="#bbb"/><rect x="3" y="8" width="6" height="4" fill="#bbb"/></svg>( 1111 ) 111 111,</div>
    <div class="contact-row"><svg width="12" height="10" viewBox="0 0 12 10"><rect x="0.5" y="0.5" width="11" height="9" fill="none" stroke="#bbb"/><path d="M0.5 0.5l5.5 5 5.5-5" stroke="#bbb" fill="none"/></svg>golpartners@info.example</div>
  </div>
  <ul class="social">
    <li><span class="dot"></span>: Friendsy</li>
    <li><span class="dot"></span>: Workline</li>
    <li><span class="dot"></span>: Searchly Plus</li>
    <li><span class="dot"></span>: Clipstream</li>
  </ul>
</footer>

<div class="bottom-bar">Copyrights @2013. GOL Partners. All Rights Reserved</div>

</body>
</html>
```